Cleaning Service Company In need of Good Web presence.

The company is a cleaning service company which provides professional staff and service for cleaning. This is a project to build a site that is both solid and a strong recognition of our organization. It is supposed to show quality, cleanliness, professionalism. The use of images and art for imagery is all good just to have a site that is consistent and solid. There might be a chance to make stationary, logo and business cars if someone feels they can build a brand that is consistent. The image we are going for is clean solid and to stand out. Finally stationary should not be expensive to print.

Current logo is attached and can be used or can be made more creative.

Target Market(s)

Corporate and Government entities, that will feel that this company has a brand that sets it apart from the rest. The company is new so the modification of the logo will not be an issue if a more solid brand come out of this project. The idea is to have a clean consistent product that stands our from others in terms of website, stationary, etc

Industry/Entity Type

Cleaning Service

Contact Information for Business Card

P.O.Box 51947
Riffa
Kingdom of Bahrain

Logo Text

Harbor Lane Services

Number of Pages Required

4 page

Font styles to use
Sans Serif

Colors
abd036
cadf82
eaf2ce
9bcb3b

Requirements
Must have
• Green Color to be used in order to stick to the name. Also the creativity and boldness in an elegant manner.
Nice to have
• Arabic name of company
• هاربر لين سرفسس ذ.م.م
• if cannot be put at least make a location should be chosen
• Also could be a bit of 3D given to the logo if it could stay elegent.
Should not have
• Should not show people cleaning.

```html
<!DOCTYPE html>
<html lang="en">
<head>
<meta charset="utf-8">
<title>Harbor Lane Services – Professional Cleaning</title>
<link href="https://fonts.googleapis.com/css2?family=Questrial&family=Open+Sans:ital,wght@0,400;0,600;1,400&display=swap" rel="stylesheet">
<style>
:root{
  --brand-deep:#23784a;
  --lime:#abd036;
  --lime-bright:#9bcb3b;
  --lime-soft:#cadf82;
  --lime-pale:#eaf2ce;
  --ink:#333;
  --muted:#666;
  --line:#dcdcdc;
  --bar:rgba(38,38,38,.86);
  --footer:#1e1e1e;
  --footer-base:#0d0d0d;
}
*{box-sizing:border-box;margin:0;padding:0}
html,body{width:1200px;height:3191px;overflow:hidden}
body{position:relative;background:#fff;font-family:"Questrial",sans-serif;color:var(--ink)}
.abs{position:absolute}
.photo{position:absolute;display:block}

/* header */
.topline{left:0;top:0;width:1200px;height:30px;background:#f4f4f2}
.hero{left:0;top:30px;width:1200px;height:470px;background:linear-gradient(100deg,#eef1ee 0%,#dfe3e0 35%,#f3efe7 65%,#e9e4da 100%)}
.header{left:0;top:30px;width:1200px;height:70px;background:var(--brand-deep)}
.brand{left:117px;top:12px;display:flex;align-items:center;gap:12px}
.brand-dot{width:86px;height:86px;border-radius:50%;background:var(--lime)}
.brand-name{font-size:17px;color:#fff;letter-spacing:.5px;margin-top:10px}
.phone-top{left:808px;top:42px;display:flex;align-items:center;gap:10px;color:#fff;font-size:15px}
.phone-top .ic{width:17px;height:17px;border-radius:50%;background:var(--lime);display:flex;align-items:center;justify-content:center}
.search{left:968px;top:41px;width:112px;height:22px;border:1.5px solid #cfe6a0;border-radius:11px;color:#9fc27a;font-size:10px;padding:4px 12px}
.nav{left:670px;top:76px;display:flex;gap:0;font-size:14px;color:#fff}
.nav a{color:#fff;text-decoration:none;position:absolute;white-space:nowrap}

/* info bar */
.infobar{left:0;top:500px;width:1200px;height:81px;background:var(--bar);display:flex}
.info{position:relative;width:400px;height:81px;display:flex;align-items:center;padding-left:85px;border-right:1px solid rgba(255,255,255,.25)}
.info:last-child{border-right:none}
.info svg{margin-right:20px}
.info h4{font-size:15px;color:#fff;font-weight:600;font-family:"Open Sans",sans-serif}
.info p{font-size:12.5px;color:#eee;margin-top:5px;font-family:"Open Sans",sans-serif}
.info .go{position:absolute;right:50px;top:30px;width:22px;height:22px;border-radius:50%;background:var(--lime-bright)}

/* section titles */
.sec-title{left:0;width:1200px;display:flex;justify-content:center;align-items:center;gap:10px;font-size:36px;color:#333}
.sec-title .rule{width:40px;height:2px;background:#444;margin-left:6px}

/* what we do */
.svc{left:85px;width:326px;height:100px;border:1px solid var(--line);background:#fff;display:flex;padding:18px 20px}
.svc.active{background:var(--lime-pale);border-color:var(--lime-soft)}
.svc svg{flex:none;margin:6px 22px 0 0}
.svc h3{font-size:15px;font-weight:400;color:#333}
.svc .bar{width:48px;height:2px;background:var(--lime);margin:7px 0 6px}
.svc p{font-size:10px;line-height:14px;color:#555;font-family:"Open Sans",sans-serif}
.card{top:734px;width:326px;height:336px;border:1px solid var(--line);background:#fff}
.card .photo{left:0;top:0;width:324px;height:187px;position:relative}
.card h3{font-size:15px;font-weight:400;margin:22px 0 0 27px}
.card .bar{width:48px;height:2px;background:var(--lime);margin:8px 0 8px 27px}
.card p{font-size:10.5px;line-height:15px;color:#555;margin:0 27px;font-family:"Open Sans",sans-serif}
.btn-more{display:inline-block;margin:14px 0 0 27px;background:var(--lime-pale);color:#555;font-size:11px;padding:7px 18px;font-family:"Open Sans",sans-serif}

/* cleaning band */
.band{left:0;top:1130px;width:1200px;height:166px;background:linear-gradient(90deg,var(--lime-bright) 0%,var(--lime) 45%,#b6d43e 100%)}
.band h3{position:absolute;left:86px;top:40px;font-size:22px;font-weight:400;color:#2b3b12;display:flex;align-items:center;gap:14px}
.band h3 .rule{width:50px;height:2px;background:#2b3b12}
.band p{position:absolute;left:86px;top:85px;width:520px;font-size:15px;line-height:27px;color:#33431a;font-family:"Open Sans",sans-serif}
.join{position:absolute;left:823px;top:53px;width:260px;height:64px;border:2px solid #2b3b12;display:flex;align-items:center;justify-content:center;font-size:27px;color:#2b3b12}

/* booking */
.book-bg{left:0;top:1873px;width:1200px;height:442px;background:linear-gradient(90deg,#7ea9c9 0%,#d7e6ec 30%,#eef0f4 55%,#e4e6ee 100%)}
.book{left:575px;top:1917px;width:535px;height:364px;background:var(--lime-pale);border:2px solid #fff}
.book .sec-title{position:absolute;top:24px;left:0;width:531px;font-size:27px}
.field{position:absolute;height:40px;background:#fff;font-size:11px;color:#aaa;padding:12px 14px;font-family:"Open Sans",sans-serif}
.submit{position:absolute;left:69px;top:300px;width:395px;height:40px;background:var(--lime-soft);filter:saturate(.55);display:flex;align-items:center;justify-content:center;font-size:14px;color:#444}

/* blog */
.post{top:2496px;width:326px}
.post .photo{position:relative;width:326px;height:209px}
.post h3{font-size:16px;font-weight:400;margin-top:17px}
.post .bar{width:48px;height:2px;background:var(--lime);margin:8px 0 10px}
.post p{font-size:10.5px;line-height:17px;color:#555;font-family:"Open Sans",sans-serif}
.post .meta{margin-top:10px;font-size:10.5px;color:#777;font-style:italic;font-family:"Open Sans",sans-serif;display:flex;gap:20px}

/* footer */
.footer{left:0;top:2900px;width:1200px;height:245px;background:var(--footer)}
.fcol{position:absolute;top:65px;color:#fff}
.fcol h4{font-size:14px;font-weight:600;font-family:"Open Sans",sans-serif}
.fcol .bar{width:30px;height:2px;background:var(--lime);margin:8px 0 14px}
.fcol p{font-size:10.5px;line-height:15px;color:#ddd;width:200px;font-family:"Open Sans",sans-serif}
.fcol ul{list-style:none;font-size:13px;font-family:"Open Sans",sans-serif}
.fcol li{height:28px;display:flex;align-items:center;gap:14px}
.fcol li::before{content:"→";color:#fff}
.vsep{position:absolute;top:60px;width:1px;height:130px;background:#444}
.sub{position:absolute;left:875px;top:115px;display:flex}
.sub .in{width:190px;height:36px;background:#ddd;font-size:10px;color:#666;padding:12px 10px;font-family:"Open Sans",sans-serif}
.sub .go{width:38px;height:36px;background:var(--lime-bright);display:flex;align-items:center;justify-content:center}
.base{left:0;top:3145px;width:1200px;height:46px;background:var(--footer-base);color:#ccc;font-size:12px;display:flex;align-items:center;justify-content:center;font-family:"Open Sans",sans-serif}
</style>
</head>
<body>

<svg width="0" height="0" style="position:absolute">
  <defs>
    <symbol id="leaf" viewBox="0 0 24 16"><path d="M1 14 C4 3 14 0 23 2 C20 11 11 16 1 14 Z" fill="#8fc03a"/><path d="M3 13 L16 5" stroke="#fff" stroke-width="1"/></symbol>
  </defs>
</svg>

<!-- Header & hero -->
<div class="abs topline"></div>
<div class="photo hero" role="img" aria-label="Bright living room with a cream sofa and a vacuum cleaner in soft daylight"></div>
<header class="abs header">
  <div class="abs brand"><span class="brand-dot"></span><span class="brand-name">Harbor Lane Services</span></div>
  <div class="abs phone-top" style="top:12px"><span class="ic"><svg width="9" height="9" viewBox="0 0 10 10"><path d="M2 1 L4 1 L4.6 3 L3.6 4 Q4.5 5.8 6 6.4 L7 5.4 L9 6 L9 8 Q5 9 1.5 4 Q1 2 2 1Z" fill="#fff"/></svg></span>(888) 420-5316</div>
  <div class="abs search" style="top:11px">Search...</div>
  <nav class="abs nav" style="top:46px;left:0">
    <a style="left:670px">Home</a><a style="left:773px">About Us</a><a style="left:893px">Services</a><a style="left:1007px">Contact Us</a>
  </nav>
</header>

<section class="abs infobar">
  <div class="info">
    <svg width="44" height="44" viewBox="0 0 44 44"><circle cx="22" cy="22" r="19" fill="none" stroke="#fff" stroke-width="2.5"/><path d="M22 10 V22 L30 27" stroke="#fff" stroke-width="2.5" fill="none"/></svg>
    <div><h4>Opening Hours</h4><p>Mon-Fri: 8:00 AM – 9:00 PM</p></div><span class="go"></span>
  </div>
  <div class="info">
    <svg width="44" height="44" viewBox="0 0 44 44"><path d="M4 22 L22 5 L40 22 M9 18 V40 H35 V18 M18 40 V28 H26 V40" stroke="#fff" stroke-width="2.5" fill="none"/></svg>
    <div><h4>Address</h4><p>18 Harbor Lane, Riffa</p></div><span class="go"></span>
  </div>
  <div class="info">
    <svg width="44" height="44" viewBox="0 0 44 44"><rect x="12" y="3" width="20" height="38" rx="3" stroke="#fff" stroke-width="2.5" fill="none"/><line x1="12" y1="33" x2="32" y2="33" stroke="#fff" stroke-width="2"/><line x1="12" y1="9" x2="32" y2="9" stroke="#fff" stroke-width="2"/></svg>
    <div><h4>Phone</h4><p>0800 51 9470</p></div><span class="go"></span>
  </div>
</section>

<!-- What we do -->
<h2 class="abs sec-title" style="top:662px;font-weight:400"><svg width="26" height="18"><use href="#leaf"/></svg>What We Do<span class="rule"></span></h2>

<div class="abs svc active" style="top:734px">
  <svg width="34" height="40" viewBox="0 0 34 40"><rect x="3" y="4" width="18" height="34" fill="none" stroke="#2e9a5a" stroke-width="2"/><rect x="21" y="14" width="10" height="24" fill="none" stroke="#2e9a5a" stroke-width="2"/><path d="M7 10h4M13 10h4M7 16h4M13 16h4M7 22h4M13 22h4M7 28h4M13 28h4" stroke="#2e9a5a" stroke-width="2"/></svg>
  <div><h3>GENERAL CLEANING</h3><div class="bar"></div><p>When you starting a company you are thinking on how to cut expenses</p></div>
</div>
<div class="abs svc" style="top:851px">
  <svg width="34" height="40" viewBox="0 0 34 40"><path d="M4 8 H24 L30 14 V36 H4 Z" fill="none" stroke="#2e9a5a" stroke-width="2"/><path d="M9 18h16M9 24h16M9 30h10" stroke="#2e9a5a" stroke-width="2"/></svg>
  <div><h3>COMMERCIALS CLEANING</h3><div class="bar"></div><p>When you starting a company you are thinking on how to cut expenses</p></div>
</div>
<div class="abs svc" style="top:968px">
  <svg width="34" height="40" viewBox="0 0 34 40"><path d="M15 6 C15 6 5 20 5 27 A10 10 0 0 0 25 27 C25 20 15 6 15 6Z" fill="none" stroke="#2e9a5a" stroke-width="2"/><path d="M27 4v8M23 8h8" stroke="#2e9a5a" stroke-width="2"/></svg>
  <div><h3>MAINTANCES SERVICES</h3><div class="bar"></div><p>When you starting a company you are thinking on how to cut expenses</p></div>
</div>

<article class="abs card" style="left:436px">
  <div class="photo" role="img" aria-label="Gloved hand wiping a wooden table with a blue cloth" style="background:linear-gradient(135deg,#3d8fc4,#7fb8dd 55%,#a2683d)"></div>
  <h3>GREEN CLEAN SERVICES</h3><div class="bar"></div>
  <p>When you starting a company you are thinking on how to cut expenses.</p>
  <span class="btn-more">Learn More</span>
</article>
<article class="abs card" style="left:787px">
  <div class="photo" role="img" aria-label="Bright apartment interior with cleaning supplies" style="background:linear-gradient(135deg,#d9d4c7,#eee9dc 50%,#5f7c4d)"></div>
  <h3>APARTMENT CLEANING</h3><div class="bar"></div>
  <p>When you starting a company you are thinking on how to cut expenses.</p>
  <span class="btn-more">Learn More</span>
</article>

<!-- Cleaning services band -->
<section class="abs band" role="img" aria-label="Lime green band with a soft cleaning scene behind">
  <h3><svg width="26" height="18"><use href="#leaf"/></svg>CLEANING SERVICES<span class="rule"></span></h3>
  <p>There are many variations of passages of Lorem ipsum available, but the majority have suffered alteration in some form</p>
  <div class="join">Join Us Now</div>
</section>

<!-- Our works -->
<h2 class="abs sec-title" style="top:1377px;font-weight:400"><svg width="26" height="18"><use href="#leaf"/></svg>Our Works<span class="rule"></span></h2>
<div class="photo" role="img" aria-label="Spray bottle and gloved hand cleaning a surface" style="left:85px;top:1458px;width:326px;height:347px;background:linear-gradient(160deg,#e8eef2,#c9d3da 50%,#6f8fb8)"></div>
<div class="photo" role="img" aria-label="Spray bottle and sponge at a window" style="left:436px;top:1458px;width:326px;height:160px;background:linear-gradient(135deg,#7a5a3a,#d8d26a 50%,#3f9a6a)"></div>
<div class="photo" role="img" aria-label="Mop on a clean floor in an office" style="left:787px;top:1458px;width:326px;height:160px;background:linear-gradient(135deg,#e9e6dc,#c6c1b3 60%,#8fa3a8)"></div>
<div class="photo" role="img" aria-label="Gloves and sponge with spray bottle" style="left:436px;top:1643px;width:326px;height:162px;background:linear-gradient(135deg,#4a9bd0,#a6d23f 55%,#e8c84a)"></div>
<div class="photo" role="img" aria-label="Mop, bucket and cloth on a wooden floor" style="left:787px;top:1643px;width:326px;height:162px;background:linear-gradient(135deg,#e6d4b6,#c89a62 55%,#b8d13a)"></div>

<!-- Service booking -->
<div class="photo book-bg" role="img" aria-label="Bucket of cleaning supplies with gloves and brushes"></div>
<form class="abs book">
  <h2 class="sec-title" style="font-weight:400"><svg width="24" height="16"><use href="#leaf"/></svg>Service Booking<span class="rule"></span></h2>
  <div class="field" style="left:69px;top:72px;width:180px">Name....</div>
  <div class="field" style="left:284px;top:72px;width:180px">Phone....</div>
  <div class="field" style="left:69px;top:134px;width:180px">Email....</div>
  <div class="field" style="left:284px;top:134px;width:180px">Date....</div>
  <div class="field" style="left:69px;top:196px;width:395px;height:80px">Message....</div>
  <div class="submit">Submit</div>
</form>

<!-- Recent blog -->
<h2 class="abs sec-title" style="top:2416px;font-weight:400"><svg width="26" height="18"><use href="#leaf"/></svg>Recent Blog<span class="rule"></span></h2>
<article class="abs post" style="left:85px">
  <div class="photo" role="img" aria-label="Cleaning a glass table by a window" style="background:linear-gradient(135deg,#c9a978,#e5e1d6 50%,#2a9bbf)"></div>
  <h3>LOREM IPSUM DOLOR</h3><div class="bar"></div>
  <p>It is a long established fact that a reader will be distracted by the readable content of a page when looking at its layout.</p>
  <div class="meta"><span>◷ 23rd may 2016</span><span>▭ 0 comments</span></div>
</article>
<article class="abs post" style="left:436px">
  <div class="photo" role="img" aria-label="Gloved hand wiping a chrome tap" style="background:linear-gradient(135deg,#dfe3e6,#b8c2c8 45%,#2ba5d0 70%,#f1d64a)"></div>
  <h3>LOREM IPSUM DOLOR</h3><div class="bar"></div>
  <p>It is a long established fact that a reader will be distracted by the readable content of a page when looking at its layout.</p>
  <div class="meta"><span>◷ 23rd may 2016</span><span>▭ 0 comments</span></div>
</article>
<article class="abs post" style="left:787px">
  <div class="photo" role="img" aria-label="Bucket of colourful cleaning supplies" style="background:linear-gradient(135deg,#f3f3f3,#8fc33c 45%,#3aa0d8 75%,#f0d040)"></div>
  <h3>LOREM IPSUM DOLOR</h3><div class="bar"></div>
  <p>It is a long established fact that a reader will be distracted by the readable content of a page when looking at its layout.</p>
  <div class="meta"><span>◷ 23rd may 2016</span><span>▭ 0 comments</span></div>
</article>

<!-- Footer -->
<footer class="abs footer">
  <div class="fcol" style="left:113px"><h4>About Us</h4><div class="bar"></div>
    <p>Totam rem aperiam, eaque ipsa quae ab illo inventore veritatis et quasi architecto beatae vitae dicta sunt explicabo. Nemo enim ipsam voluptatem quia voluptas sit.</p></div>
  <div class="vsep" style="left:355px"></div>
  <div class="fcol" style="left:418px;top:60px"><h4>Quick Links</h4><div class="bar"></div>
    <ul><li>Home</li><li>About us</li><li>Services</li><li>Contact us</li></ul></div>
  <div class="vsep" style="left:578px"></div>
  <div class="fcol" style="left:636px;top:60px"><h4>Services</h4><div class="bar"></div>
    <ul style="line-height:32px"><li style="height:32px">general cleaning</li><li style="height:32px">commercials cleaning</li><li style="height:32px">maintances services</li></ul></div>
  <div class="vsep" style="left:825px"></div>
  <div class="fcol" style="left:875px"><h4>Subscribe Newsletter</h4><div class="bar"></div></div>
  <div class="sub"><div class="in">Enter Your Email ID....</div><div class="go"><svg width="16" height="12" viewBox="0 0 16 12"><rect x="1" y="1" width="14" height="10" fill="none" stroke="#fff" stroke-width="1.5"/><path d="M1 1 L8 7 L15 1" fill="none" stroke="#fff" stroke-width="1.5"/></svg></div></div>
</footer>
<div class="abs base">harborlaneservices.com 2017. All rights reserved</div>

</body>
</html>
```